Lumavento business card

We need a modern business card - With our 4 colors - See web: www.lumavento.dk

I have attached logo and som old business Cards we have - Lets Make the new ones shine...:-) -

Industry/Entity Type

Business

Requirements
Must have
• the logo with lumavento only,

```html
<!DOCTYPE html>
<html lang="da">
<head>
<meta charset="utf-8">
<title>Lumavento business card</title>
<link rel="stylesheet" href="https://fonts.googleapis.com/css2?family=Arimo:wght@400;700&family=Questrial&family=Nunito:wght@800&display=swap">
<style>
  :root {
    --stage: #1c1c1c;
    --lime: #8cc85a;
    --lime-light: #9fd46c;
    --lime-dark: #79b548;
    --charcoal: #222222;
    --paper: #f4f4f4;
    --orange: #e07b18;
    --magenta: #b0186a;
    --purple: #6a2a6e;
    --white: #ffffff;
    --ink: #2a2a2a;
  }
  * { box-sizing: border-box; margin: 0; padding: 0; }
  html, body { width: 1200px; height: 873px; overflow: hidden; background: var(--stage); }
  .canvas { position: relative; width: 1200px; height: 873px; }

  .card { position: absolute; width: 500px; height: 300px; border-radius: 18px; overflow: hidden; }

  /* Back side */
  .card--back {
    left: 70px; top: 140px;
    background: linear-gradient(160deg, var(--lime-light), var(--lime) 55%, var(--lime-dark));
  }
  .brand-mark { display: flex; align-items: center; gap: 10px; font-family: "Questrial", sans-serif; white-space: nowrap; }
  .brand-mark__dot { width: 18px; height: 18px; border-radius: 50%; flex: none; }
  .card--back .brand-mark { position: absolute; right: 40px; top: 58px; color: var(--white); font-size: 30px; letter-spacing: 1px; }
  .card--back .brand-mark__dot { border: 2px solid var(--white); }
  .tagline { position: absolute; right: 40px; top: 118px; font-family: "Questrial", sans-serif; font-size: 21px; color: #3b4a2c; }
  .back-rule { position: absolute; right: 40px; top: 156px; width: 300px; height: 2px; background: #6a7a5c; }
  .back-web { position: absolute; right: 40px; top: 172px; font-family: "Arimo", sans-serif; font-size: 14px; letter-spacing: 7px; color: var(--white); white-space: nowrap; }

  /* Front side */
  .card--front { left: 630px; top: 420px; background: var(--charcoal); }
  .front-arc { position: absolute; left: 0; top: 0; width: 500px; height: 170px; }
  .card--front .brand-mark { position: absolute; left: 0; right: 0; top: 70px; justify-content: center; color: var(--ink); font-size: 28px; letter-spacing: 3px; }
  .card--front .brand-mark__dot { background: var(--lime); }

  .person { position: absolute; left: 20px; top: 192px; width: 186px; text-align: right; white-space: nowrap; }
  .person__name { font-family: "Nunito", sans-serif; font-weight: 800; font-size: 21px; line-height: 26px; color: var(--orange); }
  .person__role { font-family: "Arimo", sans-serif; font-weight: 700; font-size: 14px; line-height: 18px; color: var(--white); }
  .divider { position: absolute; left: 222px; top: 180px; width: 2px; height: 64px; background: linear-gradient(var(--charcoal), var(--purple), var(--charcoal)); }

  .contact { position: absolute; left: 240px; top: 178px; list-style: none; font-family: "Arimo", sans-serif; font-size: 14px; color: #e6e6e6; white-space: nowrap; }
  .contact__item { display: flex; align-items: center; gap: 10px; height: 22px; }
  .contact svg { width: 16px; height: 16px; flex: none; }
  .contact__web { display: block; height: 22px; line-height: 22px; font-weight: 700; margin-top: 4px; }
  .contact__accent { color: var(--lime); }
  .address { position: absolute; left: 0; right: 0; top: 262px; text-align: center; font-family: "Arimo", sans-serif; font-weight: 700; font-size: 14px; color: var(--magenta); white-space: nowrap; }
</style>
</head>
<body>
<main class="canvas">
  <section class="card card--back" aria-label="Back of card">
    <div class="brand-mark"><span class="brand-mark__dot"></span><span>lumavento</span></div>
    <p class="tagline">medier til unge</p>
    <div class="back-rule"></div>
    <p class="back-web">www.lumavento.dk</p>
  </section>

  <section class="card card--front" aria-label="Front of card">
    <svg class="front-arc" viewBox="0 0 500 170" preserveAspectRatio="none" aria-hidden="true">
      <path d="M0 0 H500 V40 Q250 260 0 130 Z" fill="var(--paper)"/>
    </svg>
    <div class="brand-mark"><span class="brand-mark__dot"></span><span>lumavento</span></div>

    <div class="person">
      <p class="person__name">Mette Lindvall</p>
      <p class="person__role">Director</p>
    </div>
    <div class="divider"></div>
    <ul class="contact">
      <li class="contact__item">
        <svg viewBox="0 0 16 16" aria-hidden="true"><rect x="4" y="1" width="8" height="14" rx="1.5" fill="none" stroke="var(--orange)" stroke-width="1.6"/></svg>
        <span>0412 308 517</span>
      </li>
      <li class="contact__item">
        <svg viewBox="0 0 16 16" aria-hidden="true"><rect x="1" y="3" width="14" height="10" fill="var(--orange)"/><path d="M1 3 L8 9 L15 3" fill="none" stroke="var(--charcoal)" stroke-width="1.2"/></svg>
        <span>info@lumavento.dk</span>
      </li>
      <li class="contact__web">www.<span class="contact__accent">lumavento</span>.dk</li>
    </ul>
    <p class="address">Kastanievej 18, 2000 Frederiksberg</p>
  </section>
</main>
</body>
</html>
```